KDWB Business Card

Looking for a business card design to incorporate our branding. We want to only use the colors listing in the Branding Package (attached).
Updates

Target Market(s)

People who need their phone or device fixed.

Industry/Entity Type

Electronics

Contact Information for Business Card

Please use:

Brightwick Gadget Clinic LLC
4810 E Harlow Ridge Rd
Suite 417
San Antonio, TX 78163

Marcus Delgrove, Store Manager

(210) 555-0147

Requirements
Must have
• Must include the colors that are contained within the Branding Package PDF file.

```html
<!DOCTYPE html>
<html lang="en">
<head>
<meta charset="utf-8">
<title>Brightwick Gadget Clinic Business Card</title>
<link rel="stylesheet" href="https://fonts.googleapis.com/css2?family=Ubuntu:wght@400;500;700&display=swap">
<style>
  :root {
    --orange: #e0542a;
    --rust: #a4472b;
    --peach: #f0b9a5;
    --blush: #f6d3c6;
    --mist: #ededee;
    --paper: #ffffff;
    --stage: #d9d9dc;
  }
  * { box-sizing: border-box; margin: 0; padding: 0; }
  html, body { width: 1200px; height: 1200px; overflow: hidden; }
  body {
    background: var(--stage);
    font-family: "Ubuntu", sans-serif;
    position: relative;
  }
  .card {
    position: absolute;
    top: 210px;
    width: 400px;
    height: 780px;
    border: 5px solid var(--orange);
    border-radius: 62px;
    overflow: hidden;
  }
  .card--front { left: 150px; background: var(--paper); }
  .card--back { left: 650px; }

  /* front */
  .earpiece { position: absolute; top: 58px; left: 155px; width: 80px; height: 8px; border-radius: 4px; background: var(--rust); }
  .front-camera { position: absolute; top: 54px; left: 118px; width: 16px; height: 16px; border-radius: 50%; background: var(--rust); }
  .sensor { position: absolute; top: 32px; left: 190px; width: 10px; height: 10px; border-radius: 50%; background: var(--rust); }
  .screen { position: absolute; top: 112px; left: 28px; right: 28px; height: 540px; background: var(--mist); }
  .status-bar {
    height: 26px; background: var(--orange); color: var(--paper);
    font-size: 12px; font-weight: 700;
    display: flex; justify-content: space-between; align-items: center; padding: 0 10px;
  }
  .row {
    display: flex; align-items: center; gap: 14px;
    padding: 0 18px; border-bottom: 1px solid #d6d6d8;
    background: linear-gradient(#fafafa, #e9e9eb);
  }
  .profile { height: 82px; background: var(--paper); }
  .avatar { width: 58px; height: 58px; border-radius: 50%; background: var(--rust); flex: none; }
  .person-name { color: var(--orange); font-size: 19px; font-weight: 500; letter-spacing: .5px; }
  .person-title { color: var(--rust); font-size: 14px; margin-top: 4px; }
  .company { height: 88px; }
  .company-name { color: var(--rust); font-size: 18px; font-weight: 700; line-height: 1.5; text-transform: uppercase; flex: 1; }
  .contact { height: 70px; color: var(--rust); font-size: 17px; }
  .address { height: 104px; color: var(--rust); font-size: 15px; line-height: 1.45; }
  .contact-text { flex: 1; }
  .chevron { flex: none; }
  .unlock {
    margin: 20px 18px 0; height: 62px; border: 2px solid var(--rust); border-radius: 4px;
    display: flex; align-items: center; gap: 18px; padding: 0 6px; background: var(--paper);
  }
  .unlock-knob { width: 76px; height: 46px; background: var(--rust); border-radius: 3px; display: flex; align-items: center; justify-content: center; }
  .unlock-label { color: var(--rust); font-size: 24px; }
  .call-band { position: absolute; left: 0; right: 0; bottom: 0; height: 84px; background: var(--peach); }
  .call-button {
    position: absolute; left: 40px; right: 40px; top: 24px; height: 40px; border-radius: 20px;
    background: var(--rust); color: var(--paper); font-size: 15px; font-weight: 700;
    display: flex; align-items: center; justify-content: center; gap: 30px;
  }
  .home-button { position: absolute; left: 170px; top: 680px; width: 50px; height: 50px; border-radius: 50%; border: 2px solid #c9c9cb; }

  /* back */
  .paper-texture {
    position: absolute; inset: 0;
    background: linear-gradient(180deg, #ffffff 0%, #fbf1ec 40%, var(--blush) 70%, #eea58a 100%);
  }
  .rear-camera { position: absolute; top: 42px; left: 38px; width: 40px; height: 40px; border-radius: 50%; border: 4px solid var(--orange); background: var(--rust); }
  .rear-flash { position: absolute; top: 50px; left: 96px; width: 22px; height: 22px; border-radius: 50%; background: var(--rust); }
  .brand { position: absolute; left: 46px; right: 30px; top: 560px; display: flex; align-items: center; gap: 14px; }
  .brand-mark { width: 54px; height: 54px; border-radius: 8px; background: var(--orange); flex: none; }
  .brand-name { color: var(--orange); font-size: 26px; font-weight: 400; line-height: 1.15; }
</style>
</head>
<body>

<section class="card card--front">
  <div class="sensor"></div>
  <div class="front-camera"></div>
  <div class="earpiece"></div>

  <div class="screen">
    <div class="status-bar"><span>Nexa 3G</span><span>9:41 AM</span><span>100%</span></div>

    <div class="row profile">
      <div class="avatar" role="img" aria-label="Profile portrait placeholder"></div>
      <div>
        <div class="person-name">MARCUS DELGROVE</div>
        <div class="person-title">Store Manager</div>
      </div>
    </div>

    <div class="row company">
      <div class="company-name">Brightwick Gadget<br>Clinic LLC</div>
      <svg class="chevron" width="20" height="20" viewBox="0 0 20 20"><circle cx="10" cy="10" r="9" fill="#a4472b"/><path d="M8 5l5 5-5 5" stroke="#fff" stroke-width="2.5" fill="none"/></svg>
    </div>

    <div class="row contact">
      <svg width="26" height="26" viewBox="0 0 26 26"><rect x="1" y="1" width="24" height="24" rx="3" fill="#fff" stroke="#a4472b"/><path d="M7 9c0-2 12-2 12 0v2h-3v-1h-6v1H7z M8 13h10l1 6H7z" fill="#a4472b"/></svg>
      <div class="contact-text">(210) 555-0147</div>
      <svg class="chevron" width="20" height="20" viewBox="0 0 20 20"><circle cx="10" cy="10" r="9" fill="#a4472b"/><path d="M8 5l5 5-5 5" stroke="#fff" stroke-width="2.5" fill="none"/></svg>
    </div>

    <div class="row address">
      <svg width="26" height="26" viewBox="0 0 26 26"><rect x="1" y="1" width="24" height="24" rx="3" fill="#fff" stroke="#a4472b"/><path d="M13 5l8 7h-2v8h-4v-5h-4v5H7v-8H5z" fill="#a4472b"/></svg>
      <div class="contact-text">4810 E Harlow Ridge Rd<br>Suite 417<br>San Antonio, TX 78163</div>
      <svg class="chevron" width="20" height="20" viewBox="0 0 20 20"><circle cx="10" cy="10" r="9" fill="#a4472b"/><path d="M8 5l5 5-5 5" stroke="#fff" stroke-width="2.5" fill="none"/></svg>
    </div>

    <div class="unlock">
      <div class="unlock-knob">
        <svg width="36" height="24" viewBox="0 0 36 24"><path d="M2 8h20V2l12 10-12 10v-6H2z" fill="#fff"/></svg>
      </div>
      <div class="unlock-label">slide to unlock</div>
    </div>

    <div class="call-band">
      <div class="call-button">
        <svg width="16" height="20" viewBox="0 0 16 20"><path d="M4 1l3 4-2 2c1 3 3 6 5 7l2-2 3 4-3 3C5 17 1 9 1 3z" fill="#fff"/></svg>
        <span>Call</span>
      </div>
    </div>
  </div>

  <div class="home-button"></div>
</section>

<section class="card card--back">
  <div class="paper-texture" role="img" aria-label="Crumpled paper texture fading from white to peach"></div>
  <div class="rear-camera"></div>
  <div class="rear-flash"></div>
  <div class="brand">
    <div class="brand-mark"></div>
    <div class="brand-name">Brightwick Gadget Clinic</div>
  </div>
</section>

</body>
</html>
```